Create a memorable Web Design for real estate branding

we are a Minnepolis brokerage and boutique housing specialist with over 27 years of experience in the Global furnished housing industry, servicing the Greater Los Angeles area. Specializing in “warm environments” we offer a customized approach to satisfying our guests and client’s needs by offering a wide array of options in highly desirable areas. Additionally, Lantern Dwelling Partners offers assistance and expertise to home buyers, sellers and investors.

Industry/Entity Type

Real Estate

Number of Pages Required

1 page

Font styles to use
Serif
Sans Serif
Decorative

```html
<!DOCTYPE html>
<html lang="en">
<head>
<meta charset="utf-8">
<title>Lantern Dwelling Partners</title>
<link rel="stylesheet" href="https://fonts.googleapis.com/css2?family=Open+Sans:wght@400;600;700;800&family=Roboto+Condensed:wght@400;700&family=Raleway:wght@400;600;700&display=swap">
<style>
:root{
  --teal:#0ba583;
  --teal-dark:#08916f;
  --lime:#8dc63f;
  --charcoal:#454545;
  --charcoal-soft:#5b5b5b;
  --ink:#333;
  --muted:#777;
  --paper:#fff;
  --mist:#f2f2f2;
  --line:#e1e1e1;
}
*{box-sizing:border-box;margin:0;padding:0}
html,body{width:1200px;height:2835px;overflow:hidden}
body{font-family:"Open Sans",Arial,sans-serif;color:var(--ink);background:var(--paper);position:relative}
ul{list-style:none}

/* Header */
.site-header{height:110px;position:relative;background:var(--paper)}
.brand{position:absolute;left:132px;top:22px;display:flex;align-items:center;gap:12px}
.brand-mark{width:22px;height:22px;background:var(--teal);flex:none}
.brand-name{font-weight:800;font-size:29px;line-height:1.05;color:var(--teal);letter-spacing:.5px;width:300px}
.topbar{position:absolute;right:0;top:0;width:425px;height:42px;background:var(--teal);display:flex;align-items:center;color:#fff;font-size:13px}
.topbar-phone{display:flex;align-items:center;gap:8px;padding:0 26px 0 22px;height:100%;border-right:1px solid rgba(255,255,255,.35)}
.topbar-follow{display:flex;align-items:center;gap:10px;padding-left:18px;font-family:"Roboto Condensed",sans-serif;font-size:12px;font-weight:700}
.dot-icon{width:14px;height:14px;border-radius:50%;background:#fff;opacity:.9}
.main-nav{position:absolute;right:132px;top:62px;display:flex;gap:4px;font-size:11.5px;font-weight:600}
.main-nav a{padding:9px 12px;color:var(--ink);text-decoration:none}
.main-nav a.is-active{background:var(--lime);color:#fff}

/* Hero */
.hero{height:478px;position:relative;background:linear-gradient(180deg,#1a2250 0%,#2c2f6a 35%,#3a3266 55%,#1d1c3a 80%,#121225 100%)}
.hero-arrow{position:absolute;top:330px;width:42px;height:42px;background:var(--lime);display:flex;align-items:center;justify-content:center}
.hero-arrow.prev{left:0}.hero-arrow.next{right:0}
.hero-caption{position:absolute;left:132px;top:283px;width:444px;height:117px;background:rgba(11,165,131,.88);color:#fff;font-weight:700;font-size:34px;line-height:1.25;padding:14px 30px}
.hero-dots{position:absolute;left:50%;transform:translateX(-50%);bottom:14px;display:flex;gap:11px}
.hero-dots span{width:11px;height:11px;border-radius:50%;background:#fff}
.hero-dots span.is-active{background:transparent;border:2px solid #fff;width:14px;height:14px;margin-top:-1px}

/* Services */
.services{height:310px;display:flex;justify-content:center;padding-top:32px}
.service{width:312px;text-align:center;padding:8px 20px 0;border-right:1px solid var(--line);height:240px}
.service:last-child{border-right:0}
.service-icon{width:121px;height:121px;margin:0 auto;display:block}
.service h3{color:var(--lime);font-size:17px;font-weight:700;margin:24px 0 8px}
.service p{font-size:12px;line-height:1.6;color:#555;padding:0 18px}

/* Featured */
.featured{height:444px;position:relative;background:linear-gradient(180deg,#13ad8b,#0ba583 60%,#0e9f80)}
.featured h2{text-align:center;color:#fff;font-size:24px;font-weight:700;padding-top:30px}
.featured h2::after{content:"";display:block;width:76px;height:3px;background:#fff;margin:12px auto 0}
.listings{display:flex;gap:12px;position:absolute;left:132px;top:106px}
.listing{width:225px;height:293px;background:#f4f6f8;text-align:center}
.listing-photo{height:178px}
.listing-photo.p1{background:linear-gradient(180deg,#8ab7d8,#c9b79a 60%,#6d8a4a)}
.listing-photo.p2{background:linear-gradient(180deg,#9fc4dc,#d9d2c0 55%,#5d7c3c)}
.listing-photo.p3{background:linear-gradient(180deg,#b8ccd8,#6b5a4a 55%,#9a9a98)}
.listing-photo.p4{background:linear-gradient(180deg,#cfd9e0,#7a7268 55%,#5f7b45)}
.listing address{font-style:normal;font-size:13px;color:#444;line-height:1.6;padding:14px 18px 6px}
.listing .price{font-family:"Roboto Condensed",sans-serif;font-size:23px;color:var(--lime)}
.list-arrow{position:absolute;top:223px;width:34px;height:34px;border:2px solid #fff;display:flex;align-items:center;justify-content:center}
.list-arrow.prev{left:58px}.list-arrow.next{right:58px}

/* Why */
.why{height:450px;background:var(--mist);position:relative}
.why h2{position:absolute;left:132px;top:38px;color:var(--lime);font-size:24px;font-weight:700}
.why-box{position:absolute;left:132px;top:79px;width:936px;height:314px;background:#fff;border:1px solid var(--line);display:flex}
.why-text{width:560px;padding:28px 32px;font-size:12px;line-height:1.7;color:#555}
.why-text strong{display:block;color:var(--ink);font-size:12.5px;margin-bottom:14px}
.why-text p{margin-bottom:14px}
.btn{display:inline-block;font-weight:700;font-size:12px;color:#fff;text-transform:uppercase;padding:9px 20px;letter-spacing:.3px}
.btn-lime{background:var(--lime)}
.btn-teal{background:var(--teal)}
.why-points{padding:18px 0 0 22px}
.point{display:flex;gap:18px;margin-bottom:22px}
.point-icon{width:74px;height:74px;flex:none}
.point h4{color:var(--lime);font-size:13px;font-weight:700;margin:8px 0 8px}
.point p{font-size:11.5px;color:#888;line-height:1.6;width:210px}

/* Dark band */
.band{height:334px;background:var(--charcoal);position:relative;color:#fff}
.band h3{color:var(--lime);font-size:20px;font-weight:700}
.testimonials{position:absolute;left:132px;top:34px;width:260px}
.quote{display:flex;gap:20px;margin-top:24px}
.quote-mark{font-family:Georgia,serif;font-size:64px;line-height:.7;color:#777}
.quote p{font-size:11.5px;line-height:1.75;color:#ccc;text-align:justify}
.author{display:flex;align-items:center;gap:14px;margin:18px 0 0 56px;padding-top:14px;border-top:1px solid #5a5a5a}
.avatar{width:38px;height:38px;border-radius:50%;background:linear-gradient(180deg,#aaa,#777)}
.author b{display:block;font-size:11.5px}
.author span{font-size:10.5px;color:#aaa}
.boutique{position:absolute;left:444px;top:-10px;width:312px;height:363px;background:var(--lime);text-align:center;padding-top:22px}
.boutique h3{color:#fff;font-size:22px}
.boutique .sub{font-size:15px;font-weight:600;margin-top:2px}
.boutique-photo{width:284px;height:153px;margin:18px auto 14px;background:linear-gradient(180deg,#a9c8e4,#d8c7a4 55%,#6f8b4b)}
.boutique p{font-size:12px;line-height:1.6;padding:0 44px;margin-bottom:14px}
.newsletter{position:absolute;left:794px;top:34px;width:274px}
.newsletter small{display:block;font-size:11px;color:#ccc;margin:8px 0 20px}
.field{height:40px;background:var(--charcoal-soft);display:flex;align-items:center;gap:12px;padding:0 16px;font-size:12px;color:#ddd;margin-bottom:9px}
.btn-signup{display:block;width:274px;height:48px;background:var(--teal);color:#fff;font-size:20px;font-weight:800;text-align:center;line-height:48px;margin-top:12px}

/* Call */
.call{height:378px;position:relative}
.call-box{position:absolute;left:132px;top:76px;width:936px;height:236px;border:3px solid #cfe6a9;background:#fff;text-align:center;box-shadow:0 18px 18px -14px rgba(0,0,0,.25);overflow:hidden}
.call-box h2{font-family:"Raleway",sans-serif;color:var(--teal);font-size:22px;font-weight:700;margin-top:36px}
.call-box .lead{font-family:"Raleway",sans-serif;color:#888;font-size:14px;margin-top:6px}
.skyline{position:absolute;left:0;right:0;bottom:0;height:110px;background:linear-gradient(180deg,rgba(230,230,230,0),#e4e4e4)}
.call-line{position:relative;display:flex;align-items:center;justify-content:center;gap:16px;margin-top:28px;margin-left:-60px}
.call-line .lbl{color:var(--lime);font-size:15px;font-weight:700;text-align:left}
.call-line .num{display:block;font-size:28px;color:#b6d98a;font-weight:700}

/* Footer */
.site-footer{height:331px;background:var(--teal);position:relative;color:#fff}
.footer-brand{position:absolute;left:132px;top:40px;font-weight:800;font-size:28px;line-height:1.1;width:260px}
.footer-search{position:absolute;left:132px;top:142px;width:256px;height:50px;background:#fff;display:flex;align-items:center;gap:10px;padding-left:20px;color:var(--teal);font-size:11px;font-weight:700}
.footer-col{position:absolute;top:50px}
.footer-col h4{font-size:13px;font-weight:700;margin-bottom:10px}
.footer-col li{font-size:11.5px;line-height:19.5px}
.col-menu{left:459px}.col-props{left:627px}.col-news{left:801px}
.footer-email{width:267px;height:42px;background:#fff;color:#555;font-size:11px;padding:0 18px;line-height:42px;margin-top:-4px}
.footer-signup{display:block;width:95px;margin:17px 0 0 172px;padding:9px 0;text-align:center;background:var(--lime);font-weight:700;font-size:13px}
.footer-bottom{position:absolute;left:132px;right:132px;top:278px;display:flex;justify-content:space-between;align-items:center;font-size:10px}
.follow{display:flex;align-items:center;gap:8px;font-weight:700}
.follow i{width:20px;height:20px;border-radius:50%;background:#fff;opacity:.9}
</style>
</head>
<body>

<header class="site-header">
  <div class="brand"><span class="brand-mark"></span><span class="brand-name">Lantern Dwelling Partners</span></div>
  <div class="topbar">
    <div class="topbar-phone">
      <svg width="14" height="14" viewBox="0 0 24 24"><path fill="#fff" d="M6.6 10.8a15 15 0 0 0 6.6 6.6l2.2-2.2c.3-.3.7-.4 1-.2 1.1.4 2.3.6 3.6.6.6 0 1 .4 1 1V20c0 .6-.4 1-1 1A17 17 0 0 1 3 4c0-.6.4-1 1-1h3.5c.6 0 1 .4 1 1 0 1.3.2 2.5.6 3.6.1.3 0 .7-.2 1z"/></svg>
      <span>555.2417.903</span>
    </div>
    <div class="topbar-follow">FOLLOW US ON <span class="dot-icon"></span><span class="dot-icon"></span><span class="dot-icon"></span></div>
  </div>
  <nav class="main-nav">
    <a class="is-active">HOME</a><a>ABOUT US</a><a>SERVICES</a><a>BUY</a><a>SELL</a><a>TESTIMONIALS</a><a>CONTACT US</a>
  </nav>
</header>

<section class="hero" role="img" aria-label="City skyline at night with lit towers along the harbour">
  <span class="hero-arrow prev"><svg width="14" height="14" viewBox="0 0 10 10"><path d="M7 1 3 5l4 4" fill="none" stroke="#fff" stroke-width="2"/></svg></span>
  <span class="hero-arrow next"><svg width="14" height="14" viewBox="0 0 10 10"><path d="M3 1l4 4-4 4" fill="none" stroke="#fff" stroke-width="2"/></svg></span>
  <div class="hero-caption">Specializing in<br>“warm environments”</div>
  <div class="hero-dots"><span></span><span class="is-active"></span><span></span><span></span><span></span></div>
</section>

<section class="services">
  <div class="service">
    <svg class="service-icon" viewBox="0 0 120 120"><circle cx="60" cy="60" r="55" fill="none" stroke="#0ba583" stroke-width="8"/><circle cx="60" cy="60" r="38" fill="#0ba583"/><rect x="47" y="42" width="18" height="34" fill="#fff"/><rect x="65" y="54" width="10" height="22" fill="#fff"/><g fill="#0ba583"><rect x="51" y="47" width="4" height="4"/><rect x="57" y="47" width="4" height="4"/><rect x="51" y="55" width="4" height="4"/><rect x="57" y="55" width="4" height="4"/><rect x="51" y="63" width="4" height="4"/><rect x="57" y="63" width="4" height="4"/></g></svg>
    <h3>REAL ESTATE</h3>
    <p>There are many variations of passages of Lorem Ipsum available, but the majority have suffere alteration in some.</p>
  </div>
  <div class="service">
    <svg class="service-icon" viewBox="0 0 120 120"><circle cx="60" cy="60" r="55" fill="none" stroke="#0ba583" stroke-width="8"/><circle cx="60" cy="60" r="38" fill="#0ba583"/><circle cx="56" cy="58" r="8" fill="#fff"/><path d="M42 80c0-10 6-14 14-14s14 4 14 14z" fill="#fff"/><circle cx="70" cy="44" r="8" fill="#fff"/><path d="M66 45l4-4 4 4v4h-8z" fill="#0ba583"/></svg>
    <h3>BROKERAGE</h3>
    <p>There are many variations of passages of Lorem Ipsum available, but the majority have suffere alteration in some.</p>
  </div>
  <div class="service">
    <svg class="service-icon" viewBox="0 0 120 120"><circle cx="60" cy="60" r="55" fill="none" stroke="#0ba583" stroke-width="8"/><circle cx="60" cy="60" r="38" fill="#0ba583"/><rect x="44" y="44" width="32" height="8" fill="#fff"/><rect x="46" y="52" width="28" height="24" fill="#fff"/><rect x="55" y="62" width="10" height="14" fill="#0ba583"/></svg>
    <h3>BOUTIQUE HOUSING</h3>
    <p>There are many variations of passages of Lorem Ipsum available, but the majority have suffere alteration in some.</p>
  </div>
</section>

<section class="featured" aria-label="Featured listings">
  <h2>FEATURED LISTINGS</h2>
  <span class="list-arrow prev"><svg width="12" height="12" viewBox="0 0 10 10"><path d="M7 1 3 5l4 4" fill="none" stroke="#fff" stroke-width="2"/></svg></span>
  <span class="list-arrow next"><svg width="12" height="12" viewBox="0 0 10 10"><path d="M3 1l4 4-4 4" fill="none" stroke="#fff" stroke-width="2"/></svg></span>
  <div class="listings">
    <article class="listing"><div class="listing-photo p1" role="img" aria-label="Mediterranean style house with palm trees"></div><address>4127 Alder Crest Lane, Phoenix, AZ 85021</address><div class="price">$499,900</div></article>
    <article class="listing"><div class="listing-photo p2" role="img" aria-label="Victorian house with front porch"></div><address>4127 Alder Crest Lane, Phoenix, AZ 85021</address><div class="price">$499,900</div></article>
    <article class="listing"><div class="listing-photo p3" role="img" aria-label="Modern house with wood facade"></div><address>4127 Alder Crest Lane, Phoenix, AZ 85021</address><div class="price">$499,900</div></article>
    <article class="listing"><div class="listing-photo p4" role="img" aria-label="Stone cottage style house"></div><address>4127 Alder Crest Lane, Phoenix, AZ 85021</address><div class="price">$499,900</div></article>
  </div>
</section>

<section class="why">
  <h2>WHY CHOOSE US</h2>
  <div class="why-box">
    <div class="why-text">
      <strong>Contrary to popular belief, Lorem Ipsum is not simply random text. It has roots in a piece of classical Latin literature</strong>
      <p>But I must explain to you how all this mistaken idea of denouncing pleasure and praising pain was born and I will give you a complete account of the system, and expound the actual teachings of the great explorer of the truth, the master-builder of human happiness. No one rejects, dislikes, or avoids pleasure itself, because it is pleasure</p>
      <p>At vero eos et accusamus et iusto odio dignissimos ducimus qui blanditiis praesentium voluptatum deleniti atque corrupti quos dolores.</p>
      <span class="btn btn-lime">Read more</span>
    </div>
    <div class="why-points">
      <div class="point"><svg class="point-icon" viewBox="0 0 74 74"><circle cx="37" cy="37" r="33" fill="none" stroke="#0ba583" stroke-width="5"/><circle cx="37" cy="37" r="24" fill="#0ba583"/><path d="M28 36h5v12h-5zM35 36l5-9c2 0 3 1 3 3l-1 5h6c2 0 3 2 2 3l-3 9c0 1-1 1-2 1H35z" fill="#fff"/></svg><div><h4>HEADING 1</h4><p>There are many variations of passages of Lorem Ipsum available</p></div></div>
      <div class="point"><svg class="point-icon" viewBox="0 0 74 74"><circle cx="37" cy="37" r="33" fill="none" stroke="#0ba583" stroke-width="5"/><circle cx="37" cy="37" r="24" fill="#0ba583"/><path d="M27 40a10 10 0 0 1 20 0" fill="none" stroke="#fff" stroke-width="3"/><rect x="25" y="39" width="6" height="9" rx="2" fill="#fff"/><rect x="43" y="39" width="6" height="9" rx="2" fill="#fff"/></svg><div><h4>HEADING 2</h4><p>There are many variations of passages of Lorem Ipsum available</p></div></div>
      <div class="point"><svg class="point-icon" viewBox="0 0 74 74"><circle cx="37" cy="37" r="33" fill="none" stroke="#0ba583" stroke-width="5"/><circle cx="37" cy="37" r="24" fill="#0ba583"/><rect x="27" y="29" width="18" height="18" fill="none" stroke="#fff" stroke-width="2.5"/><path d="M33 41l1-4 10-10 3 3-10 10z" fill="#fff"/></svg><div><h4>HEADING 3</h4><p>There are many variations of passages of Lorem Ipsum available</p></div></div>
    </div>
  </div>
</section>

<section class="band">
  <div class="testimonials">
    <h3>TESTIMONIALS</h3>
    <div class="quote"><span class="quote-mark">“</span><p>But I must explain to you how all this mistaken idea of denouncing pleasure and praising pain was born and I will give you a complete account of the system, and expound the actual teachings of the great explorer of the truth.</p></div>
    <div class="author"><span class="avatar" role="img" aria-label="Client portrait"></span><div><b>MARCUS HOLLOWAY</b><span>Australia</span></div></div>
  </div>
  <div class="boutique">
    <h3>BOUTIQUE HOUSING</h3>
    <div class="sub">specialist in Los Angeles</div>
    <div class="boutique-photo" role="img" aria-label="Two storey boutique home with landscaped front yard"></div>
    <p>But I must explain to you how all this mistaken idea of denouncing.</p>
    <span class="btn btn-teal">Learn more</span>
  </div>
  <div class="newsletter">
    <h3>NEWSLETTER SIGNUP!</h3>
    <small>Get more details to Signup!</small>
    <div class="field"><svg width="12" height="10" viewBox="0 0 12 10"><rect width="12" height="10" fill="#ddd"/><path d="M0 0l6 5 6-5" fill="none" stroke="#5b5b5b"/></svg>E mail id</div>
    <div class="field"><svg width="11" height="11" viewBox="0 0 11 11"><circle cx="5.5" cy="3" r="2.6" fill="#ddd"/><path d="M0 11c0-4 2.5-5 5.5-5S11 7 11 11z" fill="#ddd"/></svg>Name</div>
    <span class="btn-signup">SIGNUP!</span>
  </div>
</section>

<section class="call">
  <div class="call-box">
    <div class="skyline" role="img" aria-label="Faint city skyline silhouette"></div>
    <h2>Sed ut perspiciatis unde omnis iste natus error sit voluptatem</h2>
    <p class="lead">But I must explain to you how all this mistaken idea of denouncing</p>
    <div class="call-line">
      <svg width="48" height="48" viewBox="0 0 48 48"><circle cx="24" cy="24" r="21" fill="#fff" stroke="#8dc63f" stroke-width="3"/><path fill="#8dc63f" d="M18.6 21.8a13 13 0 0 0 5.6 5.6l1.9-1.9c.2-.2.6-.3.9-.2.9.3 2 .5 3 .5.5 0 .9.4.9.9v3c0 .5-.4.9-.9.9A14.5 14.5 0 0 1 15.5 16.1c0-.5.4-.9.9-.9h3c.5 0 .9.4.9.9 0 1.1.2 2.1.5 3.1.1.3 0 .6-.2.9z"/></svg>
      <div class="lbl">CALL US TODAY ON<span class="num">(555).2417.903</span></div>
    </div>
  </div>
</section>

<footer class="site-footer">
  <div class="footer-brand">Lantern Dwelling Partners</div>
  <div class="footer-search"><svg width="11" height="11" viewBox="0 0 12 12"><circle cx="5" cy="5" r="3.8" fill="none" stroke="#0ba583" stroke-width="1.8"/><path d="M8 8l3 3" stroke="#0ba583" stroke-width="1.8"/></svg>SEARCH</div>
  <div class="footer-col col-menu"><h4>MENU</h4><ul><li>Home</li><li>About Us</li><li>Services</li><li>Buy</li><li>Sell</li><li>Testimonials</li><li>Contact Us</li></ul></div>
  <div class="footer-col col-props"><h4>PROPERITIES</h4><ul><li>Los Angels 1</li><li>Los Angels 2</li><li>Los Angels 3</li><li>Los Angels 4</li><li>Los Angels 5</li><li>Los Angels 6</li></ul></div>
  <div class="footer-col col-news"><h4>NEWSLETTER SIGNUP!</h4><div class="footer-email">E MAIL ID</div><span class="footer-signup">SIGNUP!</span></div>
  <div class="footer-bottom">
    <div class="follow">FOLLOW US ON <i></i><i></i><i></i><i></i></div>
    <div>Copyrights @ 2016 All Rights Reserved</div>
  </div>
</footer>

</body>
</html>
```